Networking Events Calendar/Diary

We need a responsive website that can act as both an online diary/calendar and a resource for community and networking events similar to brimtolvenquarrix.com (we do not want a clone, but one with similar functionality). We need to be able to host adverts, have a client area for clients to add their own events to the diary. This needs to have the functionality that clients have to pay to add recurring events. Some integration would be useful so that if a clients already has their own online diary on their website then using an API possibly to also add that event into our online diary

Industry/Entity Type

Events

Coding

Coded - Design and coding required

Number of Pages Required

5+ page

Requirements
Must have
• My project must have a calendar area, space for ads, be responsive and easily viewable on mobile. A subscribers area for clients and a way to purchase premium status so that premium events are highlighted.

```html
<!DOCTYPE html>
<html lang="en">
<head>
<meta charset="utf-8">
<title>Varnel Events – A Resource For Networking Events</title>
<link href="https://fonts.googleapis.com/css2?family=Open+Sans:ital,wght@0,400;0,600;0,700;1,400&family=Roboto:wght@400;500;700&display=swap" rel="stylesheet">
<style>
:root{
  --topbar:#5b5a64;
  --nav:#1769ad;
  --nav-dark:#2e2e30;
  --head:#4b4b4d;
  --text:#6d6d6d;
  --title:#444;
  --line:#e3e3e3;
  --fan:#3b5998;
  --chirp:#1fa4df;
  --circle:#dd4b39;
  --gold:#d6a32e;
  --foot:#1a5f9f;
  --foot-dark:#1c1c1e;
  --brand:#1f4f8f;
}
*{box-sizing:border-box;margin:0;padding:0}
html,body{width:1200px;height:2302px;overflow:hidden;background:#fff}
body{position:relative;font-family:'Open Sans',Arial,sans-serif;color:var(--text);font-size:12px}
.abs{position:absolute}
a{color:inherit;text-decoration:none}
.topbar{left:0;top:0;width:1200px;height:31px;background:var(--topbar);color:#fff;font-size:12px}
.topbar .bulletin{left:98px;top:8px}
.topbar .links{right:0;top:0;display:flex;height:31px}
.topbar .links span{display:flex;align-items:center;gap:6px;padding:0 20px;border-left:1px solid #777}
.logo{left:98px;top:62px}
.logo .name{font-family:'Roboto',sans-serif;font-weight:700;font-size:34px;letter-spacing:3px;color:var(--brand);line-height:1}
.logo .tag{font-size:13px;color:#444;margin-top:4px}
.search{left:886px;top:70px;width:214px;height:31px;border:1px solid #e2e2e2;font-size:10px;color:#555;padding:9px 10px}
.search svg{position:absolute;right:10px;top:10px}
.nav{left:98px;top:138px;width:1002px;height:55px;background:var(--nav);border-top:3px solid #0e4f88;display:flex;box-shadow:0 8px 10px -6px rgba(0,0,0,.35)}
.nav a{color:#fff;font-size:12.5px;display:flex;align-items:center;padding:0 27px;border-right:1px solid rgba(255,255,255,.2)}
.nav a.home{background:var(--nav-dark);padding:0 22px}
.nav a:last-child{border-right:0}
.ph{background:linear-gradient(135deg,#9aa3ad,#4a5563)}
.hero{left:98px;top:223px;width:708px;height:446px;background:linear-gradient(120deg,#dfe5ea 0%,#b7c1cc 35%,#3d4f6b 70%,#1f2c45 100%)}
.hero .cap{position:absolute;left:0;bottom:0;width:615px;height:112px;background:rgba(20,20,25,.7);padding:22px 26px}
.hero h1{font-family:'Roboto',sans-serif;font-weight:700;color:#fff;font-size:26px}
.hero p{color:#eee;font-size:12px;line-height:18px;margin-top:8px;width:400px}
.hero .arrows{position:absolute;right:0;bottom:0;width:93px;height:112px;background:#174f8d;display:flex;align-items:center;justify-content:center}
.sechead{height:34px;border-bottom:1px solid var(--line)}
.sechead span{display:inline-flex;align-items:center;gap:8px;height:34px;background:var(--head);color:#fff;font-size:12.5px;padding:0 14px}
.meta{font-size:11.5px;color:#555}
.side-post .img{height:136px}
.side-post .meta{margin-top:20px}
.side-post p{font-size:11.5px;line-height:20px;margin-top:8px}
.social{display:flex;gap:10px;margin-top:20px}
.social div{width:79px;height:80px;color:#fff;text-align:center;font-size:13px;line-height:15px;padding-top:16px}
.social b{display:block;font-size:17px;margin-bottom:6px;font-weight:700}
.ad{height:117px;background:#eee}
.grid4{display:grid;grid-template-columns:repeat(2,124px);column-gap:12px;row-gap:18px}
.grid4 .img{height:82px;border:3px solid #fff;box-shadow:0 0 0 1px #ddd}
.grid4 h4{font-weight:400;font-size:13.5px;color:#333;margin-top:12px}
.grid4 p{font-size:11.5px;line-height:18px;margin-top:4px}
.feat .title{font-size:16px;color:#333;margin-top:20px}
.feat .meta{margin-top:12px}
.feat p{font-size:11.5px;line-height:17px;margin-top:14px}
.feat .more{font-size:16px;color:#444;margin-top:20px}
.mini{display:flex;gap:12px;height:121px}
.mini .img{width:111px;height:97px;flex:none}
.mini p{font-size:11.5px;line-height:20px}
.mini .meta{margin-top:8px;padding-bottom:8px;border-bottom:1px dotted #ccc;font-size:11px}
.card{left:98px;width:708px;height:194px;border:1px solid #e2e2e2;padding:9px}
.card .img{position:absolute;left:9px;top:9px;width:286px;height:176px}
.card .body{position:absolute;left:333px;top:18px;width:360px}
.card h3{font-weight:400;font-size:14px;color:#444;letter-spacing:.2px}
.card .meta{margin-top:18px;font-style:italic;display:flex;gap:22px}
.card p{font-size:11.5px;line-height:24px;margin-top:12px}
.tips-head{display:flex;justify-content:space-between;align-items:center}
.tips-img{position:relative;height:205px;background:linear-gradient(135deg,#e7c46a,#8fa0a8 55%,#3c4b55)}
.tips-img .bar{position:absolute;left:0;right:0;bottom:0;height:46px;background:rgba(20,20,20,.65);color:#fff;font-size:15px;display:flex;justify-content:space-between;align-items:center;padding:0 12px 0 22px}
.subscribe{left:0;top:1873px;width:1200px;height:101px;background:var(--gold)}
.subscribe .msg{left:166px;top:32px;display:flex;gap:18px;align-items:center;color:#fff;font-size:15px;line-height:22px}
.subscribe .field{left:516px;top:31px;width:372px;height:40px;background:#fff;border-radius:20px 0 0 20px;font-size:12px;color:#555;padding:12px 24px}
.subscribe .btn{left:888px;top:31px;width:126px;height:40px;background:#0e2a44;color:#fff;font-size:13px;border-radius:0 20px 20px 0;display:flex;align-items:center;justify-content:center}
.footer{left:0;top:1974px;width:1200px;height:273px;background:linear-gradient(180deg,#1c62a3,#175a96);color:#fff}
.footer h5{font-weight:400;font-size:19px;margin-bottom:18px}
.footer li{list-style:none;font-size:12px;line-height:25px}
.fpost{display:flex;gap:16px;margin-bottom:22px}
.fpost .img{width:62px;height:55px;border:2px solid #fff;flex:none;background:linear-gradient(135deg,#e8ddd0,#6b5e55)}
.fpost p{font-size:12px;line-height:19px}
.fpost small{font-size:10px;letter-spacing:.5px}
.follow li{display:flex;gap:16px;align-items:center;line-height:28px}
.connect li{display:flex;gap:12px;line-height:20px;margin-bottom:12px}
.bottom{left:0;top:2247px;width:1200px;height:55px;background:var(--foot-dark);color:#fff;font-size:12px}
.bottom .copy{left:98px;top:20px}
.bottom .links{left:816px;top:20px;display:flex;gap:10px;font-size:11px}
</style>
</head>
<body>

<div class="abs topbar">
  <span class="abs bulletin">Subscribe to our Weekly Bulletin</span>
  <div class="abs links">
    <span><svg width="12" height="10" viewBox="0 0 12 10"><rect x=".5" y=".5" width="11" height="9" fill="none" stroke="#fff"/><path d="M.5 .5 6 5l5.5-4.5" fill="none" stroke="#fff"/></svg>Contact Us</span>
    <span><svg width="10" height="12" viewBox="0 0 10 12"><rect y="5" width="10" height="7" fill="#fff"/><path d="M2 5V3a3 3 0 0 1 6 0" fill="none" stroke="#fff" stroke-width="1.5"/></svg>Sign In</span>
    <span style="padding-right:80px"><svg width="10" height="11" viewBox="0 0 10 11"><circle cx="5" cy="3" r="3" fill="#fff"/><path d="M0 11a5 5 0 0 1 10 0z" fill="#fff"/></svg>Registered</span>
  </div>
</div>

<div class="abs logo">
  <div class="name">VARNEL EVENTS</div>
  <div class="tag">A Resource For Networking Events</div>
</div>

<div class="abs search">SEARCH
  <svg width="11" height="11" viewBox="0 0 11 11"><circle cx="4.5" cy="4.5" r="3.5" fill="none" stroke="#333" stroke-width="1.6"/><path d="M7 7l3.5 3.5" stroke="#333" stroke-width="1.8"/></svg>
</div>

<nav class="abs nav">
  <a class="home">HOME</a><a>EVENTS BY REGION</a><a>BUSINESS SHOWS</a><a>EVENT FRANCHISES</a><a>BLOG</a><a>EVENTS FOR WOMEN</a><a>CONTACT US</a>
</nav>

<section class="abs hero" role="img" aria-label="Photo of two businessmen talking in a bright office">
  <div class="cap">
    <h1>WELCOME TO VARNEL NETWORKING EVENTS</h1>
    <p>Lorem ipsum dolor sit amet, consectetur adipiscing elit, sed do eius-mod tempor incididunt ut labore</p>
  </div>
  <div class="arrows"><svg width="40" height="24" viewBox="0 0 40 24"><path d="M12 2 2 12l10 10M28 2l10 10-10 10" fill="none" stroke="#fff" stroke-width="2.5"/></svg></div>
</section>

<!-- Upcoming events -->
<div class="abs sechead" style="left:98px;top:694px;width:708px"><span><svg width="11" height="11" viewBox="0 0 11 11"><rect y="2" width="11" height="9" fill="#fff"/><rect x="2" width="2" height="3" fill="#fff"/><rect x="7" width="2" height="3" fill="#fff"/></svg>UPCOMING EVENTS</span></div>

<article class="abs feat" style="left:98px;top:758px;width:316px">
  <div class="img" role="img" aria-label="Photo of a speaker facing a conference audience" style="height:155px;background:linear-gradient(90deg,#1d2d4a 0%,#3b4a66 35%,#c0673a 65%,#d88a4a 100%)"></div>
  <div class="title">Nemo enim ipsam voluptatem quia</div>
  <div class="meta">April 23 2015 &nbsp;&nbsp;/&nbsp;&nbsp; 2 comments &nbsp;&nbsp;/&nbsp;&nbsp; 6 hours ago</div>
  <p>At vero eos et accusamus et iusto odiossimos ducim us qui blanditiis praesentivero eos et accusamus vero eos et accusamus et. At vero eos et accusamus et iusto odiossimos ducim us qui blanditiis praesentivero</p>
  <div class="more">Continue Reading &gt;&gt;</div>
</article>

<div class="abs" style="left:443px;top:758px;width:363px">
  <div class="mini"><div class="img" role="img" aria-label="Photo of a rising bar graph on a tablet" style="background:linear-gradient(135deg,#eef3f7,#6fa6cc)"></div><div><p>At vero eos et accusamus et iusto odiossos ducim us qui blanditiis praesentivero eos et accusamus vero eos..</p><div class="meta">3 minutes ago &nbsp;&nbsp;/&nbsp;&nbsp; 0 comments</div></div></div>
  <div class="mini"><div class="img" role="img" aria-label="Photo of a businessman pointing at a chart" style="background:linear-gradient(135deg,#e3e8ee,#2d3f5c)"></div><div><p>At vero eos et accusamus et iusto odiossos ducim us qui blanditiis praesentivero eos et accusamus vero eos..</p><div class="meta">3 minutes ago &nbsp;&nbsp;/&nbsp;&nbsp; 0 comments</div></div></div>
  <div class="mini"><div class="img" role="img" aria-label="Photo of a person under a glowing light bulb" style="background:linear-gradient(135deg,#c9c9c7,#5c5a56)"></div><div><p>At vero eos et accusamus et iusto odiossos ducim us qui blanditiis praesentivero eos et accusamus vero eos..</p><div class="meta">3 minutes ago &nbsp;&nbsp;/&nbsp;&nbsp; 0 comments</div></div></div>
</div>

<!-- Latest blog posts -->
<div class="abs sechead" style="left:98px;top:1139px;width:708px"><span><svg width="12" height="11" viewBox="0 0 12 11"><path d="M1 1h10v7H5l-3 3V8H1z" fill="#fff"/></svg>LATEST BLOG POSTS</span></div>

<article class="abs card" style="top:1197px">
  <div class="img" role="img" aria-label="Photo of a woman sitting on a desk in an office" style="background:linear-gradient(135deg,#d8cfc4,#8a7e72 60%,#3d3835)"></div>
  <div class="body"><h3>NEMO ENIM IPSAM VOLUPTATEM QUIA</h3>
    <div class="meta"><span>▦ March 25, 2015</span><span>◯ 2 comments</span></div>
    <p>Lorem ipsum dolor sit amet, consectetur adipiscing elit, sed do eius-mod tempor incididunt ut labore et dolore magna aliqua. Ut enim ad minim veniam, quis nostrud exercitation ullamco laboris nisi ut aliquip ex ea commodo consequat.</p></div>
</article>
<article class="abs card" style="top:1411px">
  <div class="img" role="img" aria-label="Photo of a businessman on the phone at a laptop" style="background:linear-gradient(135deg,#f0ece6,#b9a893 50%,#3a3c47)"></div>
  <div class="body"><h3>NEMO ENIM IPSAM VOLUPTATEM QUIA</h3>
    <div class="meta"><span>▦ March 25, 2015</span><span>◯ 2 comments</span></div>
    <p>Lorem ipsum dolor sit amet, consectetur adipiscing elit, sed do eius-mod tempor incididunt ut labore et dolore magna aliqua. Ut enim ad minim veniam, quis nostrud exercitation ullamco laboris nisi ut aliquip ex ea commodo consequat.</p></div>
</article>
<article class="abs card" style="top:1626px">
  <div class="img" role="img" aria-label="Photo of a man working at a laptop in an open office" style="background:linear-gradient(135deg,#cfdbe6,#6f8ba6 50%,#2e4763)"></div>
  <div class="body"><h3>NEMO ENIM IPSAM VOLUPTATEM QUIA</h3>
    <div class="meta"><span>▦ March 25, 2015</span><span>◯ 2 comments</span></div>
    <p>Lorem ipsum dolor sit amet, consectetur adipiscing elit, sed do eius-mod tempor incididunt ut labore et dolore magna aliqua. Ut enim ad minim veniam, quis nostrud exercitation ullamco laboris nisi ut aliquip ex ea commodo consequat.</p></div>
</article>

<!-- Sidebar -->
<aside class="abs" style="left:843px;top:223px;width:258px">
  <div class="side-post">
    <div class="img" role="img" aria-label="Photo of a modern lounge with a wall of screens" style="background:linear-gradient(90deg,#c45a7a,#8d8fa6 45%,#dcdfe3)"></div>
    <div class="meta">3 minutes ago &nbsp;&nbsp;/&nbsp;&nbsp; 0 comments</div>
    <p>Lorem ipsum dolor sit amet, consectetur adiscing elit, sed do eiusmod tempor</p>
  </div>
  <div class="side-post" style="margin-top:24px">
    <div class="img" role="img" aria-label="Illustration of a man leaping with a laptop over sketches" style="background:linear-gradient(90deg,#e9e6e1,#c9c3ba)"></div>
    <div class="meta">3 minutes ago &nbsp;&nbsp;/&nbsp;&nbsp; 0 comments</div>
    <p>Lorem ipsum dolor sit amet, consectetur adiscing elit, sed do eiusmod tempor</p>
  </div>

  <div class="sechead" style="margin-top:34px;height:31px;border:0;background:var(--head);color:#fff;font-size:13px;padding:7px 14px">FOLLOW US</div>
  <div class="social">
    <div style="background:var(--fan)"><b>●</b>68,876<br>Fans</div>
    <div style="background:var(--chirp)"><b>●</b>65<br>Followers</div>
    <div style="background:var(--circle)"><b>●</b>8,961<br>Followers</div>
  </div>

  <div style="margin-top:32px;height:29px;background:var(--head);color:#fff;font-size:13px;padding:6px 14px">Ads</div>
  <div class="ad"></div>

  <div class="grid4" style="margin-top:30px">
    <div><div class="img" role="img" aria-label="Photo of hands typing on a laptop" style="background:linear-gradient(135deg,#c7d8e6,#4e6f8f)"></div><h4>Nemo enim ipsam</h4><p>Vivamus elementum semper nisi.</p></div>
    <div><div class="img" role="img" aria-label="Photo of a man with a phone on a sunny street" style="background:linear-gradient(135deg,#f2c46a,#6f7e8a)"></div><h4>Nemo enim ipsam</h4><p>Vivamus elementum semper nisi.</p></div>
    <div><div class="img" role="img" aria-label="Photo of a bearded man working outdoors" style="background:linear-gradient(135deg,#c0a98c,#4c4036)"></div><h4>Nemo enim ipsam</h4><p>Vivamus elementum semper nisi.</p></div>
    <div><div class="img" role="img" aria-label="Photo of a handshake over a desk" style="background:linear-gradient(135deg,#e6ecf1,#7d93a8)"></div><h4>Nemo enim ipsam</h4><p>Vivamus elementum semper nisi.</p></div>
  </div>

  <div class="sechead tips-head" style="margin-top:38px;height:31px">
    <span style="height:31px">NETWORKING TIPS</span>
    <svg width="22" height="12" viewBox="0 0 22 12"><path d="M6 1 1 6l5 5M16 1l5 5-5 5" fill="none" stroke="#333" stroke-width="1.5"/></svg>
  </div>
  <div class="tips-img" role="img" aria-label="Photo of a young man in a beanie looking at his phone" style="margin-top:26px">
    <div class="bar"><span>Duis aute irure</span><span>◉ &nbsp;60.223</span></div>
  </div>
  <p style="font-size:11.5px;line-height:20px;margin-top:20px">Lorem ipsum dolor sit amet, consectetur adipi-scing elit, sed do eiusmod tempor incididunt ut labore et dolore magna aliqua. Ut enim ad minim veniam, quis nostrud exercitation ullamco laboris nisi ut aliquip ex ea commodo</p>
</aside>

<!-- Subscribe band -->
<section class="abs subscribe">
  <div class="abs msg">
    <svg width="36" height="32" viewBox="0 0 36 32"><path d="M1 14 35 1 27 31 17 20z M17 20l18-19M17 20v11l5-6" fill="none" stroke="#fff" stroke-width="2" stroke-linejoin="round"/></svg>
    <span>SUBSCRIBE TO RECEIVE UPDATES AND<br>EXCLUSIVE OFFERS.</span>
  </div>
  <div class="abs field">Enter your E - mail</div>
  <div class="abs btn">SUBSCRIBE</div>
</section>

<footer class="abs footer">
  <div class="abs" style="left:98px;top:38px">
    <h5>QUICK LINKS</h5>
    <ul><li>Networking Events by Region</li><li>Networking Events by Town/City</li><li>Networking Events for Women</li><li>Workshops/Seminars</li><li>Business Shows</li><li>Networking News</li><li>Run Your Own Events</li></ul>
  </div>
  <div class="abs" style="left:362px;top:38px;width:290px">
    <h5>LATEST POST</h5>
    <div class="fpost"><div class="img" role="img" aria-label="Photo of a woman at a desk"></div><div><p>At vero eos et accusamus et iusto ucimus qui blanditiis praese</p><small>3 MINUTES AGO</small></div></div>
    <div class="fpost"><div class="img" role="img" aria-label="Photo of a man in a suit"></div><div><p>At vero eos et accusamus et iusto ucimus qui blanditiis praese</p><small>3 MINUTES AGO</small></div></div>
  </div>
  <div class="abs follow" style="left:740px;top:38px">
    <h5>FOLLOW</h5>
    <ul><li><span>■</span>Fanpage</li><li><span>■</span>Chirper</li><li><span>■</span>Circlesphere</li><li><span>■</span>Vidstream</li></ul>
  </div>
  <div class="abs connect" style="left:914px;top:38px;width:200px">
    <h5>CONNECT WITH US</h5>
    <ul>
      <li><svg width="12" height="16" viewBox="0 0 12 16" style="flex:none"><path d="M6 15S1 9 1 6a5 5 0 0 1 10 0c0 3-5 9-5 9z" fill="none" stroke="#fff" stroke-width="1.4"/><circle cx="6" cy="6" r="1.8" fill="#fff"/></svg><span>42 Orrin Lane, Calder Heights QLD 4109</span></li>
      <li><svg width="12" height="14" viewBox="0 0 12 14" style="flex:none"><path d="M2 1h3l1 3-2 1.5a8 8 0 0 0 3.5 3.5L9 7l3 1v3c0 1-1 2-2 2C5 13 0 8 0 3c0-1 1-2 2-2z" fill="#fff"/></svg><span>+1300 55 01 88</span></li>
      <li><svg width="12" height="10" viewBox="0 0 12 10" style="flex:none;margin-top:5px"><rect x=".5" y=".5" width="11" height="9" fill="none" stroke="#fff"/><path d="M.5 .5 6 5l5.5-4.5" fill="none" stroke="#fff"/></svg><span>hello@varnelevents.net</span></li>
    </ul>
  </div>
</footer>

<div class="abs bottom">
  <span class="abs copy">Copyright @ 2014 - 2015. Varnel Events. All Rights Reserved.</span>
  <div class="abs links"><span>HOME</span><span>|</span><span>ABOUT US</span><span>|</span><span>DISCLAIMER</span><span>|</span><span>CONTACT US</span><span style="margin-left:34px">C7</span></div>
</div>

</body>
</html>
```